Flyer for Compassion training days

I need a A5-size, single-sided flyer design for my training days. They are weekends in a blend of Compassionate Communication and Buddhist teachings called Gentlewise Dialogue. The logo for Gentlewise that should be included.
The flyer needs room for 1) course title, 2) course dates, location & price, 3) course description, 4) booking info, 5) my picture & short bio, and 6) the gentlewise.co website (yes, it is 'co' and not 'com).
Updates

Target Market(s)

Women 35-65 years, well-educated, spiritually minded. May have interests like yoga and meditation.

Industry/Entity Type

Health And Wellness

Font styles to use
Sans Serif
Other font styles liked:
• Blue Plaque, Josefina are both great

Colors
fbf289
fdf9cf
cfeae6
33b8a4

Requirements
Must have
• The Gentlewise logo; my picture.
• Elegance. Calm and expansive feel.
• The poster provided in the project files shows you the kind of information I need to include.
• Colours -- greens and yellows, but the options on craft plaza are not quite the right shades.
• The logo colour can be changed.
Nice to have
• Classy (but not cliche) image associated with Buddhism; gentle curves similar to those on the business card (see project files).
Should not have
• Dark background. Busy, loud design. Overly 'swirly' design. Images that I have to buy separately.

```html
<!DOCTYPE html>
<html lang="en">
<head>
<meta charset="utf-8">
<title>Gentlewise Dialogue – Core Course Flyer</title>
<link href="https://fonts.googleapis.com/css2?family=Lato:wght@400;700;900&display=swap" rel="stylesheet">
<style>
  :root {
    --teal: #1a9e8c;
    --teal-bright: #2fb5a2;
    --ink: #3a3a3a;
    --ink-dark: #222;
    --pill-dark: #3d3d3d;
    --sky-top: #c9dbe6;
    --sky-mid: #e4edf1;
    --paper: #ffffff;
    --stone-light: #d8d3c4;
    --stone-dark: #9f9a88;
    --stage: #e9ebe7;
  }
  * { box-sizing: border-box; margin: 0; padding: 0; }
  html, body { width: 1200px; height: 1199px; overflow: hidden; }
  body {
    background: var(--stage);
    font-family: "Lato", Arial, sans-serif;
    color: var(--ink);
    position: relative;
  }
  .flyer {
    position: absolute; left: 328px; top: 55px;
    width: 761px; height: 1079px;
    background: linear-gradient(180deg, var(--sky-top) 0%, var(--sky-mid) 30%, #f4f7f8 45%, var(--paper) 55%);
    overflow: hidden;
  }
  .flyer > * { position: absolute; }
  .stone-image {
    left: 560px; top: 240px; width: 201px; height: 839px;
    background: linear-gradient(180deg, #b8b09a 0%, #cdc7b4 30%, var(--stone-light) 45%, var(--stone-dark) 100%);
  }
  .ribbon-image {
    left: 520px; top: 10px; width: 241px; height: 280px;
    background: radial-gradient(ellipse at 60% 40%, rgba(26,158,140,0.35), rgba(26,158,140,0) 70%);
  }
  .curves { left: 0; top: 0; width: 761px; height: 1079px; }
  .equation {
    left: 95px; top: 48px; font-size: 28px; line-height: 30px;
    color: var(--teal); font-weight: 400;
  }
  .title {
    left: 93px; top: 118px; font-size: 58px; line-height: 55px;
    font-weight: 700; color: var(--ink);
  }
  .course-pill {
    left: 90px; top: 242px; width: 210px; height: 50px;
    background: var(--pill-dark); color: #fff;
    border-radius: 14px 4px 14px 4px;
    font-size: 26px; line-height: 50px; text-align: center;
  }
  .website {
    left: 352px; top: 256px; font-size: 24px; font-weight: 700; color: var(--ink-dark);
  }
  .event-details {
    left: 541px; top: 104px; font-size: 20px; line-height: 25px; font-weight: 700; color: var(--ink-dark);
  }
  .event-details p { margin-bottom: 8px; }
  .event-details .price { font-size: 22px; }
  .brand-mark {
    left: 50px; top: 370px; width: 170px;
    display: flex; align-items: center; gap: 8px;
    font-size: 24px; font-weight: 700; color: var(--teal-bright);
  }
  .brand-mark .dot { width: 16px; height: 16px; border-radius: 50%; background: var(--teal-bright); flex: none; }
  .intro {
    left: 228px; top: 318px; width: 320px; font-size: 18px; line-height: 24px;
  }
  .intro strong { font-weight: 700; color: var(--ink-dark); }
  .explore-heading {
    left: 92px; top: 486px; font-size: 22px; font-weight: 700; color: var(--teal);
  }
  .topics {
    left: 94px; top: 537px; width: 470px; font-size: 18px; line-height: 22px;
    font-weight: 700; color: var(--ink); list-style: none;
  }
  .topics li { position: relative; margin-bottom: 6px; }
  .topics li::before {
    content: ""; position: absolute; left: -17px; top: 9px;
    width: 6px; height: 6px; border-radius: 50%; background: var(--ink);
  }
  .audience {
    left: 93px; top: 700px; width: 460px; font-size: 17px; line-height: 22px;
  }
  .pill {
    color: #fff; font-size: 20px; text-align: center;
    border-radius: 12px 4px 12px 4px;
  }
  .pill-booking { left: 84px; top: 831px; width: 122px; height: 35px; line-height: 35px; background: var(--teal); }
  .pill-facilitator { left: 84px; top: 888px; width: 137px; height: 35px; line-height: 35px; background: var(--pill-dark); }
  .booking-text {
    left: 226px; top: 832px; font-size: 19px; line-height: 24px; font-weight: 700; color: var(--ink-dark);
  }
  .booking-text span { color: var(--teal); }
  .bio {
    left: 94px; top: 906px; width: 450px; font-size: 17px; line-height: 23.5px; text-indent: 128px;
  }
  .coaching {
    left: 96px; top: 1010px; font-size: 19px; font-weight: 700; color: var(--ink-dark);
  }
  .portrait {
    left: 560px; top: 868px; width: 172px; height: 172px; border-radius: 50%;
    background: radial-gradient(circle at 50% 45%, #a08c78, #5a4a3e);
    border: 3px solid #fff;
  }
</style>
</head>
<body>
  <article class="flyer">
    <div class="stone-image" role="img" aria-label="Photograph of a seated stone Buddha statue on a stone wall"></div>
    <div class="ribbon-image" role="img" aria-label="Flowing teal ribbon decoration"></div>

    <svg class="curves" viewBox="0 0 761 1079" aria-hidden="true">
      <path d="M0 375 C 22 430, 30 520, 100 523 L 570 523" fill="none" stroke="var(--teal)" stroke-width="3"/>
      <path d="M570 682 L 120 682 C 62 684, 42 760, 0 828" fill="none" stroke="var(--teal)" stroke-width="3"/>
      <path d="M225 893 L 470 893 C 535 893, 540 770, 575 725 C 615 676, 715 668, 761 720" fill="none" stroke="var(--pill-dark)" stroke-width="3"/>
    </svg>

    <p class="equation">Mindfullness + Kindness +<br>Compassionate Communication =</p>
    <h1 class="title">Gentlewise<br>Dialogue</h1>
    <div class="course-pill">Core Course</div>
    <p class="website">www.gentlewise.co</p>

    <div class="event-details">
      <p>11-12 Dec</p>
      <p>Rowanbank Centre,<br>Edinburgh</p>
      <p class="price">£125/100</p>
    </div>

    <div class="brand-mark"><span class="dot"></span>Gentlewise</div>

    <p class="intro"><strong>Gentlewise Dialogue</strong> can help you increase awareness &amp; compassion in everyday speech (with yourself &amp; others), better understand your own patterns, and build resilience to challenging situations. Choose from:</p>

    <h2 class="explore-heading">In this 2-day Core Course, we’ll explore:</h2>
    <ul class="topics">
      <li>Compassionate Communication;</li>
      <li>Buddhist teachings on Right Speech, loving-kindness, Right Effort, and more;</li>
      <li>mindfulness practices;</li>
      <li>choices available to us in our everyday speech.</li>
    </ul>

    <p class="audience">This workshop will be of interest if you’d like to improve personal and/or professional relationships. Open to all, best suited to those with at least 1 year’s experience with Mindfulness, Buddhism, or Compassionate Communication / NVC.</p>

    <div class="pill pill-booking">booking</div>
    <p class="booking-text">Book online at TicketMeadow or<br>write <span>marisol@gentlewise.co</span></p>

    <div class="pill pill-facilitator">facilitator</div>
    <p class="bio">Marisol Thornbury is an experienced group facilitator, having worked with a range of organisations and presented at a number of festivals &amp; conferences.</p>
    <p class="coaching">Marisol offers coaching in Gentlewise Dialogue.</p>

    <div class="portrait" role="img" aria-label="Portrait photograph of the facilitator"></div>
  </article>
</body>
</html>
```